Gaming company needs web presence

PLEASE NOTE: We need just a simple web site. We are at least a year away from launching our first product, so the site only needs a small amount of information on it. The only people who will be visiting the web site are prospective employees, prospective investors who want a little information on the company, journalists who want a little more information, and people in the games industry who will visit to read blog posts about the development of our first game.

Lanternfield Games is a new gaming company that wants to change how people think about video games. We are making games that we think can be so interesting to watch that people might want to tune into them instead of the TV.

The games we make are sophisticated, they are not for children, and we want to project an image of being serious about our craft and the brand we're trying to create. Our games are heavily focused on players interacting with each other in sophisticated ways: to negotiate, to compete, to fight, to come to each other's rescue, to cheer each other on, or to simply watch each other in awe.

We do not want a site that features lots of video game cliches like joysticks, 8 bit graphics, science fiction themes, or military themes. We are focused on craftsmanship, so we'd like to project a sense of precision, pride and deep purpose.

The purpose of this website is to create an image of our company that can help us recruit like-minded craftspeople and help find business partners. There will be no e-commerce, account creation, or forums for some time. The site should have:
-A front page that describes our business
-A section that describes our first game (we have only one for now)
-A section for employees to write blog posts. There should be something on the home page that shows links to the latest 3 blog posts.
-A section about founders that shows information about them.
-Contact information, lets people send us email

Our first game is one that looks very realistic. It takes place on a tropical island. We can't say a lot more about it in public yet, but I will say these things: it is not a game that children will play, it is not very violent, it would look more like a film than a typical video game.

And the site should be easily extendable when we have more content and more categories of content.

I've attached our official company logo with a color scheme we've been using, plus an alternate version of the logo. Please use this as a starting point for the web site's visual design. Also, I do not think it is necessary to use the dark background in the logo as the background throughout the site. I wouldn't rule it out, but I'd like to see some proposals with lighter backgrounds.

We need to be able to get code from you so that we can drop it on our server and get it running without extra effort. We need to be able to add content for Blog posts easily as well, so please indicate how that would work.
Updates

Hello everyone, Thanks for all of the great submissions so far. There are some important things I'd like to relay to everyone: We are at least a year away from launching our first game, so we only need a simple web site. Unfortunately, we can't share any screenshots or details about our first game yet. All of these submissions look great, but are far too complicated. Also, I really want to stress that we don't want to feature stock photography of people playing games, especially of children playing games. In fact, since we don't want to release any screenshots of our games and we don't have any good photography of ourselves working, it's best if there are no photographic images on the site for now.

Hello designers, Can you let me know if your designs include all the code that would let us drop the files on to our web server and easily get it up and running? Also, can you tell me how the blog posts would be created? Does your code run on a CMS? Thanks, Haskell

Hi Designers, we will be hosting this site with Wordpress, so we would prefer to have submissions ready to go on a Wordpress server. Thanks!

Target Market(s)

Investors, prospective employees, press, blog post readers.

Industry/Entity Type

Business

Font styles to use
Sans Serif

Requirements
Must have
• Simplicity first. Please use a color palette and fonts that match our logo.
Should not have
• Video game cliches. Flash animations or menus.
No children.
No photographs of people playing games.

(I realize this is very limiting, but we're keeping the sits as simple as possible for now)

```html
<!DOCTYPE html>
<html lang="en">
<head>
<meta charset="utf-8">
<title>Lanternfield Games</title>
<link href="https://fonts.googleapis.com/css2?family=Ubuntu:wght@400;500;700&display=swap" rel="stylesheet">
<style>
:root{
  --brown-dark:#4a2a0e;
  --brown-deep:#3a1f08;
  --copper:#c07838;
  --copper-light:#cd8a4e;
  --wood:#8a4a1c;
  --wood-light:#a35f2a;
  --cream:#f6ece2;
  --bio-row:#ead3bf;
  --ink:#3b2a1c;
  --text:#555;
  --orange:#e8801e;
  --green:#8ab820;
  --white:#fff;
}
*{box-sizing:border-box;margin:0;padding:0}
html,body{width:723px;height:1200px;overflow:hidden}
body{font-family:"Ubuntu",sans-serif;background:var(--white);position:relative;color:var(--text)}

/* Header */
.site-header{position:absolute;left:0;top:0;width:723px;height:95px;background:var(--brown-dark);border-bottom:3px solid var(--copper)}
.brand{position:absolute;left:105px;top:46px;color:var(--white);font-weight:700;font-size:15px;letter-spacing:.5px;display:flex;align-items:center;gap:6px;white-space:nowrap}
.brand-mark{width:10px;height:10px;background:var(--copper)}
.phone{position:absolute;left:489px;top:16px;display:flex;align-items:center;gap:8px;color:var(--white);font-size:15.5px}
.phone svg{width:16px;height:16px}
.main-nav{position:absolute;left:302px;top:62px;display:flex;height:23px}
.main-nav a{color:var(--white);text-decoration:none;font-size:8.5px;padding:0 13px;display:flex;align-items:center;border-left:1px solid rgba(255,255,255,.12)}
.main-nav a:first-child{border-left:none}
.main-nav a.active{background:var(--copper);border-radius:2px;padding:0 14px}

/* Hero */
.hero{position:absolute;left:0;top:95px;width:723px;height:233px;background:linear-gradient(120deg,#2c4f86 0%,#3a6bb0 40%,#2b5a9c 70%,#5b6e48 100%)}
.hero-title{position:absolute;left:105px;top:54px;color:var(--white);font-weight:700;font-size:32px;line-height:34px;text-shadow:0 1px 3px rgba(0,0,0,.4)}
.hero-arrow{position:absolute;top:101px;width:18px;height:18px;border-radius:50%;background:rgba(255,255,255,.7)}
.hero-dots{position:absolute;left:348px;top:335px;display:flex;gap:3px}
.hero-dots span{width:7px;height:7px;border-radius:50%;background:#ddd}
.hero-dots span.on{background:var(--copper)}

/* Welcome */
.welcome{position:absolute;left:110px;top:360px;width:503px;text-align:center}
.welcome h1{font-size:17px;font-weight:700;color:var(--brown-dark);margin-bottom:8px}
.welcome p{font-size:6.6px;line-height:10px;color:#444;margin-bottom:10px}
.btn{display:inline-flex;align-items:center;gap:4px;background:var(--copper);color:var(--white);font-size:7px;font-weight:500;border-radius:3px;padding:0 10px;height:23px}
.btn .arrow{width:9px;height:9px;border-radius:50%;background:var(--white);color:var(--copper);font-size:7px;line-height:9px;text-align:center}

/* First game */
.games{position:absolute;left:0;top:502px;width:723px;height:182px;background:linear-gradient(90deg,var(--wood) 0%,var(--wood-light) 50%,var(--wood) 100%)}
.games h2{position:absolute;top:14px;width:100%;text-align:center;color:var(--white);font-size:16px;font-weight:500}
.game-card{position:absolute;top:47px;left:281px;width:161px;text-align:center}
.game-art{height:64px;border:1px solid #e6d2bb}
.game-card h3{font-size:8px;color:var(--ink);font-weight:700;margin-top:9px}
.game-card p{font-size:6.4px;line-height:9.6px;color:#f0ddc8}

/* Blog */
.blog-heading{position:absolute;left:105px;top:723px;font-size:15px;font-weight:700}
.blog-heading .new{color:var(--green)}
.blog-heading .word{color:var(--orange)}
.post{position:absolute;left:104px;width:250px;height:48px}
.post-thumb{position:absolute;left:0;top:0;width:71px;height:48px}
.post-body{position:absolute;left:75px;top:0;width:175px}
.post-body h4{font-size:6.6px;font-weight:700;color:var(--ink)}
.post-meta{font-size:6.6px;display:flex;gap:22px;margin:3px 0 2px}
.post-meta .author{color:var(--orange);font-weight:700}
.post-body p{font-size:6.6px;line-height:9.5px;color:#666}
.divider{position:absolute;left:104px;width:250px;border-top:1px dashed #ccc}
.view-all{position:absolute;font-size:6.6px;color:var(--orange)}

/* Founders */
.founders{position:absolute;left:372px;top:711px;width:247px;height:205px;background:linear-gradient(180deg,var(--copper) 0%,var(--copper) 75%,#fff 100%)}
.founders h2{position:absolute;left:12px;top:9px;color:var(--white);font-size:12.5px;font-weight:500}
.founders .rule{position:absolute;left:0;top:30px;width:247px;border-top:1px solid var(--white)}
.bio{position:absolute;left:12px;width:222px;height:29px;display:flex}
.bio-num{width:28px;background:var(--brown-dark);color:var(--white);font-size:9px;font-weight:700;display:flex;align-items:center;justify-content:center}
.bio-text{flex:1;background:var(--bio-row);font-size:6.6px;line-height:9px;color:#444;padding:4px 6px}

/* Contact */
.contact{position:absolute;left:0;top:946px;width:723px;height:192px;background:var(--copper-light)}
.contact h2{position:absolute;left:104px;top:14px;font-size:16px;font-weight:700;color:var(--brown-deep)}
.contact-item{position:absolute;left:104px;display:flex;gap:7px;font-size:6.6px;line-height:9px;color:var(--ink)}
.contact-item svg{width:9px;height:9px;flex:none}
.field{position:absolute;background:var(--cream);font-size:6.6px;color:#bbb;padding:5px 6px;display:flex;justify-content:space-between}
.submit{position:absolute;left:567px;top:152px;width:53px;height:18px;background:var(--brown-deep);color:var(--white);border-radius:3px;font-size:7px;font-weight:700;display:flex;align-items:center;justify-content:center;gap:5px}
.submit .arrow{width:9px;height:9px;border-radius:50%;background:var(--white);color:var(--brown-deep);font-size:7px;line-height:9px;text-align:center}

/* Footer */
.site-footer{position:absolute;left:0;top:1138px;width:723px;height:62px;background:var(--brown-dark)}
.site-footer .brand{top:26px;font-size:13px}
.legal{position:absolute;left:395px;top:26px;font-size:6.8px;color:var(--white)}
.social{position:absolute;left:551px;top:24px;display:flex;gap:10px}
.social span{width:10px;height:10px;border-radius:50%;background:var(--white)}
</style>
</head>
<body>

<header class="site-header">
  <div class="brand"><span class="brand-mark"></span>LANTERNFIELD GAMES</div>
  <div class="phone">
    <svg viewBox="0 0 16 16"><circle cx="8" cy="8" r="7" fill="none" stroke="#c07838" stroke-width="1.3"/><path d="M5.5 4.8l1.2-.3.8 1.8-.8.6a5 5 0 0 0 2.4 2.4l.6-.8 1.8.8-.3 1.2c-3.2.2-5.9-2.5-5.7-5.7z" fill="#c07838"/></svg>
    +0800 555 0192
  </div>
  <nav class="main-nav">
    <a class="active">Home</a><a>About Us</a><a>Services</a><a>Blog</a><a>Reviews</a><a>Contact Us</a>
  </nav>
</header>

<section class="hero" role="img" aria-label="Tabletop strategy board with a blue sea map and wooden ship pieces">
  <h2 class="hero-title">we wants to change<br>how people think<br>about video games</h2>
  <span class="hero-arrow" style="left:16px"></span>
  <span class="hero-arrow" style="left:688px"></span>
</section>
<div class="hero-dots"><span class="on"></span><span></span><span></span></div>

<section class="welcome">
  <h1>WELCOME TO LANTERNFIELD GAMES</h1>
  <p>Morbi tincidunt pulvinar orci, sollicitudin interdum magna commodo tristique. Aenean rutrum auctor tortor, eget condimentum lectus dapibus pretium. In tristique nulla eu pellentesque condimentum. Duis sagittis sed magna vel facilisis. Curabitur gravida id neque et vestibulum. Vivamus placerat eu dui eu mollis. Nam feugiat enim mauris, at suscipit enim ultricies eu.</p>
  <p>Nam porta congue quam, interdum ornare lacus iaculis eu. Duis luctus adipiscing feugiat. In cursus sapien mauris, id eleifend neque dignissim nec.</p>
  <span class="btn">View more <span class="arrow">›</span></span>
</section>

<section class="games">
  <h2>Our First Game</h2>
  <article class="game-card">
    <div class="game-art" role="img" aria-label="Preview artwork of the first game" style="background:linear-gradient(135deg,#8a7a5a,#b09070,#5a6a8a)"></div>
    <h3>DICTUM AUCTOR PURUS</h3>
    <p>Nulla neque urna, feugi at ac leo non, blandit aucto Phasellus dictum auctor purus. Nulla neque urna, feugiat ac leo non, blandit auctor magna.</p>
  </article>
</section>

<h2 class="blog-heading"><span class="new">New</span>&nbsp; <span class="word">Blog</span></h2>
<article class="post" style="top:750px">
  <div class="post-thumb" role="img" aria-label="Board game close-up" style="background:linear-gradient(135deg,#6a5a2a,#b0a040)"></div>
  <div class="post-body">
    <h4>PHASELLUS DICTUM AUCTOR</h4>
    <div class="post-meta"><span class="author">&#9679; Mara Ellison</span><span>&#9719; July 14, 2014</span></div>
    <p>Nulla neque urna, feugiat ac leo non, blandit auctor magna. Sed auctor elit nisl, ut elementum justo placerat sit amet...</p>
  </div>
</article>
<div class="divider" style="top:804px"></div>
<article class="post" style="top:809px">
  <div class="post-thumb" role="img" aria-label="Card game spread on a table" style="background:linear-gradient(135deg,#8a6a9a,#c0a080)"></div>
  <div class="post-body">
    <h4>PHASELLUS DICTUM AUCTOR</h4>
    <div class="post-meta"><span class="author">&#9679; Mara Ellison</span><span>&#9719; July 10, 2014</span></div>
    <p>Nulla neque urna, feugiat ac leo non, blandit auctor magna. Sed auctor elit nisl, ut elementum justo placerat sit amet...</p>
  </div>
</article>
<div class="divider" style="top:863px"></div>
<article class="post" style="top:868px">
  <div class="post-thumb" role="img" aria-label="Game pieces on a wooden table" style="background:linear-gradient(135deg,#8a4a1c,#c8a070)"></div>
  <div class="post-body">
    <h4>PHASELLUS DICTUM AUCTOR</h4>
    <div class="post-meta"><span class="author">&#9679; Mara Ellison</span><span>&#9719; July 06, 2014</span></div>
    <p>Nulla neque urna, feugiat ac leo non, blandit auctor magna. Sed auctor elit nisl, ut elementum justo placerat sit amet...</p>
  </div>
</article>
<span class="view-all" style="left:320px;top:922px">View all »</span>

<aside class="founders">
  <h2>Founders BIOS</h2>
  <div class="rule"></div>
  <div class="bio" style="top:43px"><span class="bio-num">01</span><span class="bio-text">Nulla neque urna, feugiat ac leo non, blandit auctor magna. Sed auctor elit nisl,</span></div>
  <div class="bio" style="top:75px"><span class="bio-num">02</span><span class="bio-text">Nulla neque urna, feugiat ac leo non, blandit auctor magna. Sed auctor elit nisl,</span></div>
  <div class="bio" style="top:107px"><span class="bio-num">03</span><span class="bio-text">Nulla neque urna, feugiat ac leo non, blandit auctor magna. Sed auctor elit nisl,</span></div>
  <div class="bio" style="top:139px"><span class="bio-num">04</span><span class="bio-text">Nulla neque urna, feugiat ac leo non, blandit auctor magna. Sed auctor elit nisl,</span></div>
  <div class="bio" style="top:171px"><span class="bio-num">05</span><span class="bio-text">Nulla neque urna, feugiat ac leo non, blandit auctor magna. Sed auctor elit nisl,</span></div>
</aside>
<span class="view-all" style="left:386px;top:922px">View all »</span>

<section class="contact">
  <h2>Contact Us</h2>
  <div class="contact-item" style="top:48px">
    <svg viewBox="0 0 10 10"><path d="M5 0a3.5 3.5 0 0 0-3.5 3.5C1.5 6 5 10 5 10s3.5-4 3.5-6.5A3.5 3.5 0 0 0 5 0z" fill="#e8801e"/></svg>
    <span>52, Etiam sit amet magna nec quam<br>venenatis vehicula ut sed nisl.</span>
  </div>
  <div class="contact-item" style="top:73px">
    <svg viewBox="0 0 10 10"><path d="M2 1l2 .2.6 2.2-1 .8a6 6 0 0 0 2.2 2.2l.8-1 2.2.6L9 8c-4 .6-7.6-3-7-7z" fill="#e8801e"/></svg>
    <span>+0800 555 0192</span>
  </div>
  <div class="contact-item" style="top:89px">
    <svg viewBox="0 0 10 10"><rect x="0" y="2" width="10" height="7" fill="#e8801e"/><path d="M0 2l5 4 5-4" stroke="#c98448" fill="none"/></svg>
    <span>hello@lanternfield.com</span>
  </div>
  <div class="field" style="left:280px;top:42px;width:109px;height:20px"><span>Name</span><span>&#9679;</span></div>
  <div class="field" style="left:395px;top:42px;width:109px;height:20px"><span>Email</span><span>&#9993;</span></div>
  <div class="field" style="left:511px;top:42px;width:109px;height:20px"><span>Phone</span><span>&#9743;</span></div>
  <div class="field" style="left:280px;top:70px;width:340px;height:71px"><span>Message</span><span>&#9632;</span></div>
  <div class="submit">Submit <span class="arrow">›</span></div>
</section>

<footer class="site-footer">
  <div class="brand"><span class="brand-mark"></span>LANTERNFIELD GAMES</div>
  <div class="legal">© 2014 All Rights Reserved &nbsp;|&nbsp; Privacy Policy</div>
  <div class="social"><span></span><span></span><span></span><span></span></div>
</footer>

</body>
</html>
```